3rd Annual Suds & Wags Fundraiser

This is our 3rd Annual Suds & Wags Dog Wash Extravagana to support Helpers of Tamsin Valley Pet Center. Please see the attached flyer for the 2nd Annual. We loved this flyer! Please revamp with our logo attached and the new content provided. Let's keep to the same colors as the 2nd Annual flyer-no change. Date: Saturday April 25th 2020 10A-1PM. Rain Date: May 2nd. Same address as 2nd Annual.

Other font styles liked:
• See 2nd Annual Flyer

Colors
add136
e34297
6b449b

Requirements
Must have
• See attached 2nd annual flyer including colors
Nice to have

```html
<!DOCTYPE html>
<html lang="en">
<head>
<meta charset="utf-8">
<title>3rd Annual Suds &amp; Wags Doggie Wash Extravaganza</title>
<link href="https://fonts.googleapis.com/css2?family=Baloo+2:wght@700;800&family=Open+Sans:ital,wght@0,400;0,600;0,700;1,600&family=Great+Vibes&display=swap" rel="stylesheet">
<style>
:root{
  --green:#add136;
  --pink:#e34297;
  --purple:#6b449b;
  --ink:#1d1d1d;
  --white:#ffffff;
  --bg:#d9d9d9;
}
*{margin:0;padding:0;box-sizing:border-box}
html,body{width:1200px;height:1200px;overflow:hidden;background:var(--bg)}
body{font-family:"Open Sans",Arial,sans-serif;color:var(--ink)}
.flyer{position:absolute;left:204px;top:40px;width:791px;height:1120px;background:var(--white);overflow:hidden}
.abs{position:absolute}
.art{position:absolute;left:0;top:0}
.headline{font-family:"Baloo 2",Arial,sans-serif;font-weight:800;line-height:1}
.edition{left:45px;top:412px;font-size:44px;color:var(--pink)}
.event-name{left:45px;top:462px;font-size:40px;color:var(--purple)}
.tagline{left:46px;top:502px;font-size:11.5px;letter-spacing:4.2px;color:var(--pink);font-weight:600}
.subtitle{left:45px;top:515px;font-size:36px;color:#8cb524}
.ribbon{left:0;top:570px;width:552px;height:46px;background:var(--purple);border-radius:0 23px 23px 0;color:var(--white);font-family:"Baloo 2",Arial,sans-serif;font-weight:800;font-size:27px;line-height:48px;padding-left:45px}
.label{font-family:"Baloo 2",Arial,sans-serif;font-weight:800;font-size:29px;color:var(--pink);line-height:1}
.value{font-size:19.5px;font-weight:600;line-height:1.35}
.support{left:575px;top:438px;width:165px;text-align:center}
.support .lead{font-size:19px;font-weight:600}
.partner-mark{display:flex;align-items:center;gap:10px;margin:18px 0 14px;justify-content:center}
.partner-mark .dot{width:30px;height:30px;border-radius:50%;background:var(--ink);flex:none}
.partner-mark .name{font-size:16px;font-weight:700;line-height:1.15;color:var(--ink);text-align:left}
.support .motto{font-family:Georgia,serif;font-size:12px;line-height:1.5}
.perks{top:766px;font-size:15px;font-weight:600;line-height:19.5px;list-style:none}
.perks li{padding-left:20px;position:relative}
.perks li svg{position:absolute;left:0;top:5px}
.donate-line{left:45px;top:838px;font-size:15px;font-weight:700}
.donate-line .url{color:var(--white)}
.donate-btn{left:520px;top:828px;width:107px;height:40px;background:var(--white);border:2px solid var(--purple);display:flex;align-items:center;gap:6px;padding-left:5px}
.donate-btn .sq{width:26px;height:30px;background:var(--purple);flex:none}
.donate-btn .txt{font-size:14px;font-weight:700;line-height:1.05;color:var(--purple)}
.notes{left:45px;top:870px;font-size:14.3px;font-style:italic;font-weight:600;line-height:20px}
.contact{top:940px;width:290px;text-align:center;font-size:15px;line-height:19.5px}
.contact .who{font-size:20px;font-weight:700;color:var(--purple);line-height:26px}
.signed{font-family:"Great Vibes",cursive;font-size:24px;color:var(--purple);margin-top:4px}
.org-mark{display:flex;align-items:center;justify-content:center;gap:8px;margin-top:4px}
.org-mark .dot{width:18px;height:18px;flex:none}
.org-mark .name{font-size:14px;font-weight:700;color:var(--ink);line-height:1.15}
</style>
</head>
<body>
<main class="flyer">

  <svg class="art" width="791" height="1120" viewBox="0 0 791 1120">
    <defs>
      <linearGradient id="yard" x1="0" y1="0" x2="1" y2="1">
        <stop offset="0" stop-color="#4f6b3a"/><stop offset=".5" stop-color="#9aa58e"/><stop offset="1" stop-color="#c9c6bf"/>
      </linearGradient>
      <linearGradient id="group" x1="0" y1="0" x2="0" y2="1">
        <stop offset="0" stop-color="#7aa35a"/><stop offset="1" stop-color="#b8a79a"/>
      </linearGradient>
      <linearGradient id="bath" x1="0" y1="0" x2="1" y2="1">
        <stop offset="0" stop-color="#9c6a52"/><stop offset="1" stop-color="#d4b49a"/>
      </linearGradient>
    </defs>
    <rect role="img" aria-label="Volunteers washing a small white dog on a driveway" x="0" y="0" width="791" height="460" fill="url(#yard)"/>
    <path d="M0,392 C150,340 350,420 560,412 C660,410 740,380 791,352 L791,1120 L0,1120 Z" fill="var(--white)"/>
    <path d="M0,392 C150,340 350,420 560,412 C660,410 740,380 791,352" fill="none" stroke="var(--pink)" stroke-width="7"/>
    <path role="img" aria-label="Group of student volunteers with a dog mascot" d="M0,0 H364 V120 Q220,260 0,180 Z" fill="url(#group)"/>
    <path d="M364,120 Q220,260 0,180" fill="none" stroke="var(--pink)" stroke-width="7"/>
    <circle role="img" aria-label="German shepherd being hosed down" cx="125" cy="324" r="77" fill="#6f7a4a" stroke="var(--pink)" stroke-width="3"/>
    <circle role="img" aria-label="Children posing with a dog mascot" cx="302" cy="290" r="90" fill="#a58a62" stroke="var(--pink)" stroke-width="3"/>
    <circle role="img" aria-label="Puppy wrapped in a white towel" cx="478" cy="380" r="101" fill="#b9b7b3" stroke="var(--pink)" stroke-width="3"/>
    <rect role="img" aria-label="Line drawing of a dog with bubbles" x="268" y="395" width="112" height="105" rx="40" fill="#eef6d8"/>
    <rect x="0" y="752" width="791" height="172" fill="var(--green)"/>
    <path role="img" aria-label="Girl bathing a cocker spaniel" d="M560,1120 C640,1000 680,820 791,740 V1120 Z" fill="url(#bath)"/>
    <path d="M560,1120 C640,1000 680,820 791,740" fill="none" stroke="var(--pink)" stroke-width="6"/>
  </svg>

  <div class="abs headline edition">3rd Annual</div>
  <div class="abs headline event-name">Suds &amp; Wags</div>
  <div class="abs tagline">DO A LITTLE. CHANGE A LOT.</div>
  <div class="abs headline subtitle">Doggie Wash Extravaganza</div>
  <div class="abs ribbon">A Family Fun Event For All Ages</div>

  <div class="abs label" style="left:45px;top:637px">Date:</div>
  <div class="abs value" style="left:135px;top:640px">Saturday April 25th 2020<br>Rain Date: May 2nd</div>
  <div class="abs label" style="left:45px;top:700px">Time:</div>
  <div class="abs value" style="left:135px;top:704px">10AM-1PM</div>

  <div class="abs label" style="left:418px;top:637px">Location:</div>
  <div class="abs value" style="left:418px;top:664px;line-height:26px">Brookline Realty, 418 Harbor Crest<br>Ave. Tamsin Valley FL 32990<br>Wren Lake Town Center</div>

  <section class="abs support">
    <div class="lead">In Support Of</div>
    <div class="partner-mark"><span class="dot"></span><span class="name">Helpers of<br>Tamsin Valley<br>Pet Center</span></div>
    <div class="motto">Adopt a forever friend …<br>You will be their hero</div>
  </section>

  <ul class="abs perks" style="left:50px">
    <li><svg width="13" height="10" viewBox="0 0 13 10"><path d="M1,5 L5,9 L12,1" fill="none" stroke="var(--pink)" stroke-width="2.5"/></svg>FREE Doggie Wash</li>
    <li><svg width="13" height="10" viewBox="0 0 13 10"><path d="M1,5 L5,9 L12,1" fill="none" stroke="var(--pink)" stroke-width="2.5"/></svg>Food &amp; Beverages</li>
    <li><svg width="13" height="10" viewBox="0 0 13 10"><path d="M1,5 L5,9 L12,1" fill="none" stroke="var(--pink)" stroke-width="2.5"/></svg>Vendors (FREE give-a-ways)</li>
  </ul>
  <ul class="abs perks" style="left:302px">
    <li><svg width="13" height="10" viewBox="0 0 13 10"><path d="M1,5 L5,9 L12,1" fill="none" stroke="var(--pink)" stroke-width="2.5"/></svg>Raffle Drawings</li>
    <li><svg width="13" height="10" viewBox="0 0 13 10"><path d="M1,5 L5,9 L12,1" fill="none" stroke="var(--pink)" stroke-width="2.5"/></svg>Grand Prize</li>
    <li><svg width="13" height="10" viewBox="0 0 13 10"><path d="M1,5 L5,9 L12,1" fill="none" stroke="var(--pink)" stroke-width="2.5"/></svg>Donations Welcome</li>
  </ul>
  <ul class="abs perks" style="left:556px">
    <li><svg width="13" height="10" viewBox="0 0 13 10"><path d="M1,5 L5,9 L12,1" fill="none" stroke="var(--pink)" stroke-width="2.5"/></svg>Adoptions by<br>HOTVPC</li>
  </ul>

  <div class="abs donate-line">To Make a Donation: <span class="url">https://www.example.com/hotvpc/</span></div>
  <div class="abs donate-btn"><span class="sq"></span><span class="txt">Click<br>Donate</span></div>

  <div class="abs notes">All domestic breeds from puppies to seniors invited.<br>Please be sure Furry Fido is tolerant of other dogs, crowds and bathing.</div>

  <section class="abs contact" style="left:36px">
    <div class="who">Marlene Hadley</div>
    <div>Brookline Realty Corp.</div>
    <div>555.201.4836</div>
    <div style="font-size:14px">marlenehadley@brooklinerealtycorp.com</div>
    <div class="signed">Marlene Hadley</div>
    <div class="org-mark"><svg class="dot" viewBox="0 0 18 18"><rect width="18" height="18" fill="var(--ink)"/></svg><span class="name">Brookline Realty</span></div>
  </section>

  <section class="abs contact" style="left:304px">
    <div class="who">Denise Calloway</div>
    <div>HOTVPC</div>
    <div>555.478.9012</div>
    <div>denise-calloway@example.net</div>
    <div class="org-mark" style="margin-top:14px"><svg class="dot" viewBox="0 0 18 18"><circle cx="9" cy="9" r="9" fill="var(--ink)"/></svg><span class="name" style="text-align:left">Helpers of Tamsin Valley<br>Pet Center</span></div>
  </section>

</main>
</body>
</html>
```